RTavenor Business Cards & Letterhead

I have a logo but need a design for some new business cards. We are a Design-Build Firm that specializes in the design and construction of commercial projects.
the cards need to be professional. no cartoon stuff.
i would like to have the cards in AI format so I can update the card as needed. Logo is provided.
Our Address is: 4187 Marlowe Ct. Apex, North Carolina 27614

```html
<!DOCTYPE html>
<html lang="en">
<head>
<meta charset="utf-8">
<title>RTavenor Business Card</title>
<link rel="stylesheet" href="https://fonts.googleapis.com/css2?family=Open+Sans:wght@400;600;700;800&display=swap">
<style>
  :root {
    --stage: #333333;
    --card-dark: #202126;
    --card-dark-soft: #272b33;
    --brand-blue: #1a7cc4;
    --brand-blue-bright: #1f8fd8;
    --back-blue-center: #127ac0;
    --back-blue-edge: #093a63;
    --back-word: #0a3c66;
    --logo-grey: #6d6e73;
    --text-white: #ffffff;
  }
  * { margin: 0; padding: 0; box-sizing: border-box; }
  html, body { width: 1200px; height: 780px; overflow: hidden; }
  body {
    background: var(--stage);
    font-family: "Open Sans", Arial, sans-serif;
    position: relative;
  }
  .card {
    position: absolute;
    top: 230px;
    width: 560px;
    height: 320px;
    overflow: hidden;
  }
  /* Back side */
  .card-back {
    left: 30px;
    background: radial-gradient(ellipse at 55% 50%, var(--back-blue-center) 0%, #0d5890 45%, var(--back-blue-edge) 100%);
    display: flex;
    align-items: center;
    justify-content: center;
  }
  .back-wordmark {
    font-weight: 800;
    font-size: 64px;
    letter-spacing: 2px;
    color: var(--back-word);
  }
  /* Front side */
  .card-front {
    left: 610px;
    background: var(--card-dark);
  }
  .front-decoration {
    position: absolute;
    right: 30px;
    top: 40px;
    width: 220px;
    height: 240px;
    border-radius: 28px;
    background: var(--card-dark-soft);
  }
  .front-logo {
    position: absolute;
    left: 34px;
    top: 46px;
    display: flex;
    align-items: center;
    gap: 10px;
  }
  .logo-square {
    width: 26px;
    height: 26px;
    background: var(--brand-blue);
  }
  .logo-name {
    font-weight: 800;
    font-size: 32px;
    letter-spacing: 1px;
    color: var(--logo-grey);
    line-height: 1;
  }
  .person {
    position: absolute;
    right: 0;
    top: 118px;
    display: flex;
    align-items: stretch;
  }
  .person-text { text-align: right; padding-right: 10px; }
  .person-name {
    font-weight: 800;
    font-size: 23px;
    color: var(--brand-blue);
    letter-spacing: 0.5px;
    line-height: 1.1;
  }
  .person-title {
    font-weight: 600;
    font-size: 14px;
    color: var(--text-white);
    margin-top: 2px;
  }
  .person-bar {
    width: 22px;
    background: linear-gradient(90deg, var(--brand-blue), var(--brand-blue-bright));
  }
  .address {
    position: absolute;
    left: 44px;
    top: 168px;
    font-size: 14px;
    line-height: 1.35;
    color: var(--text-white);
  }
  .contacts {
    position: absolute;
    left: 50px;
    top: 236px;
    list-style: none;
    font-size: 14px;
    line-height: 1.45;
    color: var(--text-white);
  }
  .contacts li { display: flex; align-items: center; gap: 8px; }
  .contacts svg { width: 13px; height: 13px; fill: var(--brand-blue); flex: none; }
</style>
</head>
<body>
  <section class="card card-back" aria-label="Card back">
    <span class="back-wordmark">RTAVENOR</span>
  </section>

  <section class="card card-front" aria-label="Card front">
    <div class="front-decoration"></div>

    <div class="front-logo">
      <span class="logo-square"></span>
      <span class="logo-name">RTAVENOR</span>
    </div>

    <div class="person">
      <div class="person-text">
        <div class="person-name">ROLAND TAVENOR</div>
        <div class="person-title">Founder/President</div>
      </div>
      <div class="person-bar"></div>
    </div>

    <p class="address">4187 Marlowe Ct. Apex,<br>North Carolina 27614</p>

    <ul class="contacts">
      <li>
        <svg viewBox="0 0 24 24" aria-hidden="true"><path d="M6.6 10.8a15.1 15.1 0 0 0 6.6 6.6l2.2-2.2a1 1 0 0 1 1-.25 11.4 11.4 0 0 0 3.6.57 1 1 0 0 1 1 1V20a1 1 0 0 1-1 1A17 17 0 0 1 3 4a1 1 0 0 1 1-1h3.5a1 1 0 0 1 1 1c0 1.25.2 2.45.57 3.57a1 1 0 0 1-.25 1z"/></svg>
        (919) 555-0148
      </li>
      <li>
        <svg viewBox="0 0 24 24" aria-hidden="true"><path d="M12 2a10 10 0 1 0 0 20 10 10 0 0 0 0-20zm6.9 6h-3a15.7 15.7 0 0 0-1.4-3.6A8 8 0 0 1 18.9 8zM12 4c.8 1.2 1.5 2.5 1.9 4h-3.8c.4-1.5 1.1-2.8 1.9-4zM4.3 14a8 8 0 0 1 0-4h3.4a16.5 16.5 0 0 0 0 4zm.8 2h3a15.7 15.7 0 0 0 1.4 3.6A8 8 0 0 1 5.1 16zm3-8h-3a8 8 0 0 1 4.4-3.6A15.7 15.7 0 0 0 8.1 8zM12 20c-.8-1.2-1.5-2.5-1.9-4h3.8c-.4 1.5-1.1 2.8-1.9 4zm2.3-6H9.7a14.7 14.7 0 0 1 0-4h4.6a14.7 14.7 0 0 1 0 4zm.2 5.6a15.7 15.7 0 0 0 1.4-3.6h3a8 8 0 0 1-4.4 3.6zm1.8-5.6a16.5 16.5 0 0 0 0-4h3.4a8 8 0 0 1 0 4z"/></svg>
        www.rtavenor.com
      </li>
      <li>
        <svg viewBox="0 0 24 24" aria-hidden="true"><path d="M3 5h18a1 1 0 0 1 1 1v12a1 1 0 0 1-1 1H3a1 1 0 0 1-1-1V6a1 1 0 0 1 1-1zm9 7.5L4 7.3V17h16V7.3zM5.2 7 12 11.2 18.8 7z"/></svg>
        RWT@RTavenor.com
      </li>
    </ul>
  </section>
</body>
</html>
```